New Flyer Design Project

We need a flyer update targeting the hotel and hospitality industry. The focus is on the experience of a customer coming to a hotel with self-cleaning surfaces and highlighting those benefits throughout the facility. Our product can be applied to ANY surface and is a Long Lasting technology. 1. Odor Free Hotel rooms 2. Slip resistant flooring 3. Self-Cleaning Exteriors --see attached brief for some ideas. The handout needs to target the hotel owners and management. Imagine checking into a hotel and finding out your room is protected by a self cleaning technology that uses light to clean. Eliminating toxic cleaners from your space.

Target Market(s)

Hotel and Hospitality industry.

Industry/Entity Type

Casino, Hotels, Cruise Ships, theme parks etc.

Requirements
Must have
• Hotel and other hospitality images

```html
<!DOCTYPE html>
<html lang="en">
<head>
<meta charset="utf-8">
<title>NovaShield Hotel Flyer</title>
<link href="https://fonts.googleapis.com/css2?family=Montserrat:wght@400;500;600;700;800&family=Oswald:wght@400;500;600;700&display=swap" rel="stylesheet">
<style>
  :root{
    --navy:#13244d;
    --navy-deep:#0c1836;
    --yellow:#f6b818;
    --white:#ffffff;
    --ink:#1c2540;
    --muted:#4a5470;
    --page:#eceef1;
    --line:#d9dde6;
  }
  *{box-sizing:border-box;margin:0;padding:0}
  html,body{width:1200px;height:2180px;overflow:hidden;background:var(--page)}
  body{position:relative;font-family:"Montserrat",Arial,sans-serif;color:var(--ink)}
  .flyer{position:absolute;left:50px;top:312px;width:1100px;height:1556px;background:var(--white);overflow:hidden;box-shadow:0 10px 30px rgba(0,0,0,.12)}
  .hero-photo{position:absolute;left:0;top:0;width:1100px;height:720px;
    background:linear-gradient(180deg,#5a7fb8 0%,#7f9ecb 28%,#c9a27a 52%,#6b5a4c 70%,#2d4f6a 86%,#1d3850 100%)}
  .brand{position:absolute;left:70px;top:0;width:330px;height:150px;background:var(--navy);display:flex;align-items:center;justify-content:center;gap:14px;border-bottom:6px solid var(--yellow)}
  .brand-mark{width:26px;height:26px;background:var(--yellow)}
  .brand-name{font-family:"Montserrat",Arial,sans-serif;font-weight:700;font-size:40px;color:var(--white)}
  .headline{position:absolute;left:0;top:390px;width:1100px;height:250px;background:rgba(12,24,54,.78);text-align:center;padding-top:26px}
  .headline .lead{font-family:"Oswald",Arial,sans-serif;font-weight:400;font-size:38px;letter-spacing:6px;color:var(--white)}
  .headline .main{font-family:"Oswald",Arial,sans-serif;font-weight:700;font-size:72px;line-height:1.05;color:var(--white);letter-spacing:1px}
  .headline .accent{display:inline-block;margin-top:8px;padding:2px 26px;background:var(--yellow);font-family:"Oswald",Arial,sans-serif;font-weight:700;font-size:60px;line-height:1.1;color:var(--navy)}
  .photo-row{position:absolute;left:60px;top:680px;width:980px;height:250px;display:flex;gap:14px}
  .photo{height:250px;border:6px solid var(--white);box-shadow:0 4px 10px rgba(0,0,0,.2)}
  .photo.lobby{width:400px;background:linear-gradient(135deg,#8b6a4a,#c9a47a 55%,#4e3b2c)}
  .photo.bath{width:276px;background:linear-gradient(135deg,#e3e1dc,#a9a39a 60%,#6d665e)}
  .photo.room{width:276px;background:linear-gradient(135deg,#f0ece4,#c8b89e 55%,#7d6a55)}
  .section-title{position:absolute;left:70px;top:970px;font-family:"Oswald",Arial,sans-serif;font-weight:700;font-size:40px;color:var(--navy);letter-spacing:1px}
  .section-title::after{content:"";display:block;width:90px;height:5px;background:var(--yellow);margin-top:6px}
  .benefits{position:absolute;left:70px;top:1060px;width:960px;display:grid;grid-template-columns:repeat(3,1fr);column-gap:30px;row-gap:26px}
  .benefit{display:flex;align-items:center;gap:14px;font-size:19px;font-weight:600;line-height:1.3;color:var(--ink)}
  .benefit svg{flex:0 0 48px}
  .tagline-row{position:absolute;left:70px;top:1350px;width:960px;display:flex;align-items:center;justify-content:space-between}
  .tagline{font-family:"Oswald",Arial,sans-serif;font-weight:700;font-size:44px;color:var(--navy)}
  .tagline span{color:var(--yellow)}
  .badges{display:flex;gap:22px}
  .badge{width:74px;height:74px;border-radius:50%;background:var(--line);border:4px solid var(--navy)}
  .footer{position:absolute;left:0;bottom:0;width:1100px;height:90px;background:var(--navy-deep);border-top:8px solid var(--yellow);display:flex;align-items:center;justify-content:space-around;color:var(--white);font-size:18px;font-weight:500}
  .footer .item{display:flex;align-items:center;gap:10px}
</style>
</head>
<body>
  <article class="flyer">
    <div class="hero-photo" role="img" aria-label="Hotel exterior at dusk with a lit pool and palm trees"></div>

    <div class="brand">
      <span class="brand-mark"></span>
      <span class="brand-name">NovaShield</span>
    </div>

    <header class="headline">
      <p class="lead">EXPERIENCE OF COMING</p>
      <h1 class="main">TO A HOTEL WITH</h1>
      <p class="accent">SELF-CLEANING SURFACES</p>
    </header>

    <div class="photo-row">
      <div class="photo lobby" role="img" aria-label="Warm hotel lobby interior"></div>
      <div class="photo bath" role="img" aria-label="Clean hotel bathroom with bathtub"></div>
      <div class="photo room" role="img" aria-label="Bright hotel guest room"></div>
    </div>

    <h2 class="section-title">OUR TECHNOLOGY DELIVERS</h2>

    <ul class="benefits">
      <li class="benefit"><svg width="48" height="48" viewBox="0 0 48 48"><circle cx="24" cy="24" r="22" fill="#f6b818"/><path d="M14 25l7 7 13-15" stroke="#13244d" stroke-width="4" fill="none" stroke-linecap="round" stroke-linejoin="round"/></svg>Promote Self Cleaning Surfaces in Hotel Rooms</li>
      <li class="benefit"><svg width="48" height="48" viewBox="0 0 48 48"><circle cx="24" cy="24" r="22" fill="#f6b818"/><path d="M14 25l7 7 13-15" stroke="#13244d" stroke-width="4" fill="none" stroke-linecap="round" stroke-linejoin="round"/></svg>Odor Free Spaces – Eliminate Smoke and Chemical Smells</li>
      <li class="benefit"><svg width="48" height="48" viewBox="0 0 48 48"><circle cx="24" cy="24" r="22" fill="#f6b818"/><path d="M14 25l7 7 13-15" stroke="#13244d" stroke-width="4" fill="none" stroke-linecap="round" stroke-linejoin="round"/></svg>Reduce Cleaning Expenses</li>
      <li class="benefit"><svg width="48" height="48" viewBox="0 0 48 48"><circle cx="24" cy="24" r="22" fill="#f6b818"/><path d="M14 25l7 7 13-15" stroke="#13244d" stroke-width="4" fill="none" stroke-linecap="round" stroke-linejoin="round"/></svg>VOC and SVOC Free Spaces</li>
      <li class="benefit"><svg width="48" height="48" viewBox="0 0 48 48"><circle cx="24" cy="24" r="22" fill="#f6b818"/><path d="M14 25l7 7 13-15" stroke="#13244d" stroke-width="4" fill="none" stroke-linecap="round" stroke-linejoin="round"/></svg>Slip Resistant Surfaces</li>
      <li class="benefit"><svg width="48" height="48" viewBox="0 0 48 48"><circle cx="24" cy="24" r="22" fill="#f6b818"/><path d="M14 25l7 7 13-15" stroke="#13244d" stroke-width="4" fill="none" stroke-linecap="round" stroke-linejoin="round"/></svg>Green Cleaners Work Better</li>
      <li class="benefit"><svg width="48" height="48" viewBox="0 0 48 48"><circle cx="24" cy="24" r="22" fill="#f6b818"/><path d="M14 25l7 7 13-15" stroke="#13244d" stroke-width="4" fill="none" stroke-linecap="round" stroke-linejoin="round"/></svg>Prevent Mold/ Mildew Stains</li>
    </ul>

    <div class="tagline-row">
      <p class="tagline">ALWAYS CLEANING, <span>ALL THE TIME</span></p>
      <div class="badges">
        <span class="badge"></span>
        <span class="badge"></span>
      </div>
    </div>

    <footer class="footer">
      <span class="item"><svg width="20" height="20" viewBox="0 0 24 24"><path d="M6.6 10.8a15 15 0 006.6 6.6l2.2-2.2a1 1 0 011-.25 11.4 11.4 0 003.6.57 1 1 0 011 1V20a1 1 0 01-1 1A17 17 0 013 4a1 1 0 011-1h3.5a1 1 0 011 1c0 1.25.2 2.45.57 3.57a1 1 0 01-.25 1z" fill="#f6b818"/></svg>+1 800 555 0142</span>
      <span class="item"><svg width="20" height="20" viewBox="0 0 24 24"><path d="M6.6 10.8a15 15 0 006.6 6.6l2.2-2.2a1 1 0 011-.25 11.4 11.4 0 003.6.57 1 1 0 011 1V20a1 1 0 01-1 1A17 17 0 013 4a1 1 0 011-1h3.5a1 1 0 011 1c0 1.25.2 2.45.57 3.57a1 1 0 01-.25 1z" fill="#f6b818"/></svg>+1 555 010 2233</span>
      <span class="item"><svg width="20" height="20" viewBox="0 0 24 24"><rect x="2" y="5" width="20" height="14" rx="2" fill="#f6b818"/><path d="M2 6l10 7 10-7" stroke="#0c1836" stroke-width="2" fill="none"/></svg>hello@novashieldcoat.com</span>
      <span class="item">www.novashieldcoat.com</span>
    </footer>
  </article>
</body>
</html>
```